Classy, Elegant, Simple Business Card Design

Looking to have a classy, simple, and elegant design. Want a top notch designed business card. I really like the look of the new torvane credit card. I also like the design I attached. I am trying to reach 21-29 year old females for booking us for there wedding or event. We offer Disc Jockey Service, Photo Booth Rentals, and Uplighting .

Target Market(s)

21-28 year old females

Contact Information for Business Card

Has to have logo, website, email, and phone number

Font styles to use
Other font styles liked:
• open to font choice, modern, clean
Designer to choose
33a6d7
0791cd
0555a3
ffffff

Requirements
Must have
• Has to have logo, website, email, and phone number
Nice to have
• I really like the design of the new torvane credit card. I also included my logo and some designs I like
Should not have
• clutter or too much info

```html
<!DOCTYPE html>
<html lang="en">
<head>
<meta charset="utf-8">
<title>Tidecrest Event Group – Business Card</title>
<link rel="stylesheet" href="https://fonts.googleapis.com/css2?family=Lato:wght@300;400;700&display=swap">
<style>
  :root {
    --stage: #2b2c2e;
    --card-light: #ffffff;
    --card-dark: #1a1c1f;
    --ink: #1f2226;
    --rule: #9a9ea3;
    --blue-bright: #33a6d7;
    --blue: #0791cd;
    --blue-deep: #0555a3;
  }
  * { margin: 0; padding: 0; box-sizing: border-box; }
  html, body { width: 1200px; height: 1108px; overflow: hidden; }
  body {
    background: var(--stage);
    font-family: "Lato", Arial, sans-serif;
    display: flex;
    align-items: center;
    justify-content: center;
    gap: 80px;
  }
  .card {
    width: 440px;
    height: 760px;
    border-radius: 30px;
    position: relative;
  }
  .card-front {
    background: var(--card-light);
    color: var(--ink);
    display: flex;
    flex-direction: column;
    align-items: center;
    text-align: center;
  }
  .brand {
    margin-top: 190px;
    display: flex;
    flex-direction: column;
    align-items: center;
  }
  .brand-name {
    font-size: 44px;
    font-weight: 700;
    color: var(--blue-deep);
    letter-spacing: 1px;
    line-height: 1;
  }
  .brand-line {
    font-size: 17px;
    font-weight: 400;
    color: var(--blue-deep);
    letter-spacing: 9px;
    margin-top: 10px;
  }
  .contact-icons {
    margin-top: 190px;
    width: 330px;
    display: flex;
    align-items: center;
    gap: 10px;
  }
  .contact-icons .rule { flex: 1; height: 1px; background: var(--rule); }
  .contact-icons svg { width: 28px; height: 28px; display: block; }
  .contact-list {
    list-style: none;
    margin-top: 18px;
    font-size: 21px;
    line-height: 1.3;
  }
  .divider {
    width: 250px;
    height: 1px;
    background: var(--ink);
    margin: 18px 0 14px;
  }
  .services {
    font-size: 21px;
    line-height: 1.3;
  }
  .card-back {
    background: var(--card-dark);
  }
  .back-name {
    position: absolute;
    left: 0; right: 0;
    top: 470px;
    text-align: center;
    font-size: 30px;
    font-weight: 700;
    color: var(--blue);
    letter-spacing: 1px;
  }
</style>
</head>
<body>
  <section class="card card-front" aria-label="Business card front">
    <div class="brand">
      <span class="brand-name">TIDECREST</span>
      <span class="brand-line">EVENT GROUP</span>
    </div>

    <div class="contact-icons">
      <span class="rule"></span>
      <svg viewBox="0 0 28 28" aria-label="Phone">
        <circle cx="14" cy="14" r="14" fill="var(--blue)"/>
        <path d="M9 8.5c1-.8 2-.6 2.4.3l1 2c.3.6.1 1.2-.4 1.6l-.8.6c.7 1.6 1.9 2.8 3.5 3.5l.6-.8c.4-.5 1-.7 1.6-.4l2 1c.9.4 1.1 1.4.3 2.4-.9 1.1-2.3 1.3-3.8.6-3-1.4-5.4-3.8-6.8-6.8-.7-1.5-.5-2.9.6-3.8z" fill="#fff"/>
      </svg>
      <svg viewBox="0 0 28 28" aria-label="Email">
        <circle cx="14" cy="14" r="14" fill="var(--blue)"/>
        <rect x="7" y="9" width="14" height="10" rx="1" fill="none" stroke="#fff" stroke-width="1.6"/>
        <path d="M7.5 9.8 14 14.8l6.5-5" fill="none" stroke="#fff" stroke-width="1.6"/>
      </svg>
      <svg viewBox="0 0 28 28" aria-label="Website">
        <circle cx="14" cy="14" r="14" fill="var(--blue)"/>
        <circle cx="14" cy="14" r="7" fill="none" stroke="#fff" stroke-width="1.5"/>
        <ellipse cx="14" cy="14" rx="3" ry="7" fill="none" stroke="#fff" stroke-width="1.3"/>
        <path d="M7 14h14" stroke="#fff" stroke-width="1.3"/>
      </svg>
      <span class="rule"></span>
    </div>

    <ul class="contact-list">
      <li>044-555 210 347</li>
      <li>info@tidecrest.com</li>
      <li>www.tidecrestevents.com</li>
    </ul>

    <div class="divider"></div>

    <p class="services">Disc Jockey Service | Uplighting<br>Photo Booth Rentals</p>
  </section>

  <section class="card card-back" aria-label="Business card back">
    <span class="back-name">TIDECREST</span>
  </section>
</body>
</html>
```